Workforce Equity Lens Poster for staff

Our organization has developed an equity lens to be used by staff when implementing new programs and services. We need a poster that will be used as a quick reference for staff to use on a daily basis and will hang in cubicles. We'd like the main six questions to stand out with the subsequent questions less prominent. Looking for a poster that is 11 x 17 inches.

Industry/Entity Type

Equity

Font styles to use
Sans Serif

Colors

Designer to choose colors to be used in the design.

Requirements
Must have
• Easy to read. Not too text heavy, so any way to highlight the main six questions. It would be great to have some sort of icon or illustration with each of the six questions.
Nice to have
• Illustrative design features.
Should not have
• No photos of people.

```html
<!DOCTYPE html>
<html lang="en">
<head>
<meta charset="utf-8">
<title>Cedar County Workforce System Equity Lens</title>
<link rel="stylesheet" href="https://fonts.googleapis.com/css2?family=Lato:wght@400;700;900&display=swap">
<style>
  :root {
    --ink: #1f1f1f;
    --body: #3a3a3a;
    --paper-top: #ffffff;
    --paper-bottom: #e9e9e9;
    --dark: #2d2d2d;
    --darker: #1c1c1c;
    --band: #141414;
    --light-text: #e6e6e6;
    --icon-bg: #f4f4f4;
    --icon-ink: #5a5a5a;
  }
  * { box-sizing: border-box; margin: 0; padding: 0; }
  html, body { width: 797px; height: 1200px; overflow: hidden; }
  body { font-family: "Lato", sans-serif; background: #ffffff; }
  .poster {
    position: relative; width: 797px; height: 1200px; overflow: hidden;
    background: linear-gradient(180deg, var(--paper-top) 0%, var(--paper-bottom) 55%);
  }
  .brand-tab { position: absolute; top: 0; right: 0; width: 520px; height: 112px; }
  .brand {
    position: absolute; top: 26px; right: 46px; display: flex; align-items: center; gap: 16px;
    color: #ffffff; font-weight: 700;
  }
  .brand-mark { width: 44px; height: 44px; border-radius: 50%; background: #ffffff; }
  .brand-name { font-size: 25px; line-height: 1.15; letter-spacing: 0.5px; }
  .brand-name span { display: block; font-size: 15px; letter-spacing: 7px; }

  .intro { position: absolute; top: 126px; left: 52px; right: 52px; }
  .intro h2 { font-size: 31px; font-weight: 900; color: var(--ink); margin: 0 0 8px; line-height: 1.2; }
  .intro p { font-size: 14.5px; line-height: 1.45; color: var(--body); margin-bottom: 10px; text-align: justify; }
  .intro h2.second { margin-top: 16px; }

  .lens { position: absolute; left: 0; right: 0; top: 690px; bottom: 0; background: var(--dark); }
  .lens-shape { position: absolute; left: 0; top: 640px; width: 797px; height: 80px; }
  .lens-title {
    position: absolute; top: 652px; left: 0; right: 0; height: 60px;
    display: flex; align-items: center; justify-content: center;
    color: #ffffff; font-weight: 900; font-size: 30px; letter-spacing: 0.3px;
  }
  .questions { position: absolute; top: 726px; left: 44px; right: 44px; list-style: none; }
  .question { display: flex; align-items: center; gap: 22px; height: 76px; }
  .question-icon {
    flex: none; width: 64px; height: 64px; border-radius: 50%; background: var(--icon-bg);
    border: 3px solid #8a8a8a; display: flex; align-items: center; justify-content: center;
  }
  .question-icon svg { width: 38px; height: 38px; }
  .question-text { font-size: 14.5px; line-height: 1.4; color: var(--light-text); }
  .question-text strong { color: #ffffff; font-weight: 900; font-size: 16px; text-transform: uppercase; letter-spacing: 0.3px; }
</style>
</head>
<body>
<main class="poster">
  <svg class="brand-tab" viewBox="0 0 520 112" aria-hidden="true">
    <path d="M0 0 H520 V112 H90 C50 112 40 60 0 0 Z" fill="var(--darker)"/>
  </svg>
  <div class="brand">
    <div class="brand-mark"></div>
    <div class="brand-name">RIDGELINE WORKFORCE<span>ALLIANCE</span></div>
  </div>

  <section class="intro">
    <h2>What is equity?</h2>
    <p>In workforce development, equity is the notion that everyone has the opportunity to obtain quality, living wage employment or be placed in employment-related training regardless of their national origin, race, gender, sexual orientation, disability, first language or other distinguishing characteristic. Different approaches to delivery of workforce services may be necessary in order for each customer to achieve success in training or employment.</p>
    <h2 class="second">What is an equity lens?</h2>
    <p>An equity lens is a practical tool that will help ensure that policies, programs, decisions, or proposed actions in Cedar County’s workforce system result in equitable outcomes for all job seekers. This lens shall be used by the Ridgeline Workforce Alliance Board of Directors and Executive Board when making policy decisions or decisions on how to allocate funding. It shall also be used by Ridgeline Workforce Alliance staff, JobPath Cedar staff, and other workforce system partners when creating and implementing programs.</p>
    <p>The purpose of the equity lens is to provide a tool to assist the Board and staff with identifying potentially negative outcomes for policies, programs, decisions, or actions that could increase disparities for under-represented populations. An equity lens is not meant to be a road block to effectively delivering workforce services, but rather a mechanism to identify and remove systemic barriers for under-represented populations as it relates to workforce-related services.</p>
  </section>

  <div class="lens"></div>
  <svg class="lens-shape" viewBox="0 0 797 80" aria-hidden="true">
    <path d="M0 30 L797 0 V80 H0 Z" fill="var(--dark)"/>
    <path d="M0 22 L797 4 V72 L0 78 Z" fill="var(--band)"/>
  </svg>
  <h1 class="lens-title">Cedar County Workforce System Equity Lens</h1>

  <ol class="questions">
    <li class="question">
      <div class="question-icon"><svg viewBox="0 0 40 40"><rect x="9" y="6" width="22" height="30" rx="2" fill="none" stroke="var(--icon-ink)" stroke-width="3"/><rect x="15" y="3" width="10" height="6" rx="1" fill="var(--icon-ink)"/><path d="M14 16h12M14 22h12M14 28h8" stroke="var(--icon-ink)" stroke-width="2.5"/></svg></div>
      <p class="question-text"><strong>Who is affected?</strong> Who are the groups affected by this policy, metric, program, decision, or proposed action? How will each group be affected? Is any group negatively affected in a disproportionate way?</p>
    </li>
    <li class="question">
      <div class="question-icon"><svg viewBox="0 0 40 40"><rect x="6" y="22" width="28" height="5" fill="var(--icon-ink)"/><circle cx="12" cy="14" r="4" fill="var(--icon-ink)"/><circle cx="28" cy="14" r="4" fill="var(--icon-ink)"/><circle cx="20" cy="11" r="4" fill="var(--icon-ink)"/><path d="M10 27v8M30 27v8" stroke="var(--icon-ink)" stroke-width="3"/></svg></div>
      <p class="question-text"><strong>Are they at the table?</strong> How have you actively involved stakeholders who are also members of the communities affected by the policy, metric, program, decision, or proposed action?</p>
    </li>
    <li class="question">
      <div class="question-icon"><svg viewBox="0 0 40 40"><rect x="5" y="12" width="30" height="9" fill="none" stroke="var(--icon-ink)" stroke-width="3"/><path d="M10 12l6 9M18 12l6 9M26 12l6 9" stroke="var(--icon-ink)" stroke-width="2.5"/><path d="M10 21v14M30 21v14" stroke="var(--icon-ink)" stroke-width="3"/></svg></div>
      <p class="question-text"><strong>What are the barriers?</strong> What are the societal or organizational barriers that prevent a population from being successful?</p>
    </li>
    <li class="question">
      <div class="question-icon"><svg viewBox="0 0 40 40"><path d="M6 8l6 6M12 8l-6 6" stroke="var(--icon-ink)" stroke-width="3"/><circle cx="30" cy="30" r="4" fill="none" stroke="var(--icon-ink)" stroke-width="3"/><path d="M9 34c4-10 18-8 18-22" fill="none" stroke="var(--icon-ink)" stroke-width="3" stroke-dasharray="4 3"/><path d="M22 12l5-5 5 5" fill="none" stroke="var(--icon-ink)" stroke-width="3"/></svg></div>
      <p class="question-text"><strong>What are population-specific strategies?</strong> To address any inequities, do we have solutions that are tailored to work for the disproportionately affected groups? Have we used the ‘Platinum Rule’?</p>
    </li>
    <li class="question">
      <div class="question-icon"><svg viewBox="0 0 40 40"><path d="M8 34L20 20M20 20L30 6M20 20l12 4M20 20l-4-14M20 20l14-8" stroke="var(--icon-ink)" stroke-width="3" fill="none"/><circle cx="20" cy="20" r="3" fill="var(--icon-ink)"/></svg></div>
      <p class="question-text"><strong>Are there unintended consequences?</strong> Does this policy, program, decision, or proposed action ignore or worsen existing disparities or produce other unintended consequences?</p>
    </li>
    <li class="question">
      <div class="question-icon"><svg viewBox="0 0 40 40"><path d="M8 22l8 8 16-18" fill="none" stroke="var(--icon-ink)" stroke-width="4"/></svg></div>
      <p class="question-text"><strong>How do we measure success in a population-specific way?</strong> Describe how data about the policy, metric, program, decision, or proposed action, and its impact (positive or negative) on equitable access and outcomes, will be monitored and evaluated?</p>
    </li>
  </ol>
</main>
</body>
</html>
```